Animal Eye Clinic needs a Business card

We are a new veterinary ophthalmology practice (Ridgeline Pet Vision Care) and we need a business card designed. We only see animal eyes - we are not a regular veterinary clinic. We already have a logo. We are looking for a professional, good looking business card to hand out to our clients. We are looking for something simple but professional and contemporary. Our logo is likely the only picture/graphic that needs to be on the card.
Updates

Contact Information for Business Card

Delia Vossman, BSc, DVM, MSc, DipACVO
Veterinary Ophthalmologist

Phone: 250.418.3927
Email: ridgelinepetvisioncare@mailbox-example.net
Website: ridgelinepetvisioncare-example.net
Address: 1874 Thornbury Rd
Kelowna, BC, V1X 4M9

Colors

Designer to choose colors to be used in the design.

Requirements
Must have
• Our logo (attached)

```html
<!DOCTYPE html>
<html lang="en">
<head>
<meta charset="utf-8">
<title>Ridgeline Pet Vision Care – Business Card</title>
<link rel="stylesheet" href="https://fonts.googleapis.com/css2?family=Open+Sans:wght@400;600;700&display=swap">
<style>
  :root {
    --bg: #2a2a2c;
    --card-white: #ffffff;
    --card-grey: #7b7b7d;
    --teal: #0f93a3;
    --text-light: #ffffff;
    --shadow: rgba(0,0,0,0.35);
  }
  html, body {
    margin: 0;
    padding: 0;
    width: 1200px;
    height: 960px;
    overflow: hidden;
    background: var(--bg);
    font-family: "Open Sans", Arial, sans-serif;
  }
  .canvas {
    position: relative;
    width: 1200px;
    height: 960px;
  }
  .card {
    position: absolute;
    left: 240px;
    width: 720px;
    height: 411px;
    border-radius: 26px;
    box-shadow: 0 10px 30px var(--shadow);
    overflow: hidden;
  }
  /* Front */
  .card-front {
    top: 46px;
    background: var(--card-white);
    display: flex;
    align-items: center;
    justify-content: center;
  }
  .wordmark {
    display: flex;
    align-items: center;
    gap: 22px;
    color: var(--teal);
    font-weight: 700;
  }
  .wordmark-dot {
    width: 74px;
    height: 74px;
    border-radius: 50%;
    background: var(--teal);
  }
  .wordmark-text {
    display: flex;
    flex-direction: column;
    line-height: 1.05;
  }
  .wordmark-top {
    font-size: 22px;
    letter-spacing: 14px;
  }
  .wordmark-main {
    font-size: 40px;
    letter-spacing: -0.5px;
  }
  /* Back */
  .card-back {
    top: 503px;
    background: var(--card-grey);
    color: var(--text-light);
  }
  .contact {
    position: absolute;
    left: 56px;
    bottom: 48px;
    font-size: 17px;
    line-height: 1.4;
  }
  .contact p { margin: 0; }
  .contact .name {
    font-weight: 700;
    font-size: 20px;
  }
  .contact .creds {
    font-weight: 600;
    font-size: 13px;
  }
  .contact .role {
    font-weight: 600;
    margin-bottom: 26px;
  }
  .contact .address { margin-bottom: 18px; }
  .back-mark {
    position: absolute;
    right: 52px;
    top: 54px;
    display: flex;
    align-items: center;
    gap: 14px;
    color: var(--text-light);
    font-weight: 700;
    font-size: 22px;
  }
  .back-mark-dot {
    width: 40px;
    height: 40px;
    border-radius: 50%;
    background: var(--teal);
  }
</style>
</head>
<body>
<main class="canvas">
  <section class="card card-front" aria-label="Card front">
    <div class="wordmark">
      <span class="wordmark-dot" aria-hidden="true"></span>
      <div class="wordmark-text">
        <span class="wordmark-top">RIDGELINE</span>
        <span class="wordmark-main">PET VISION CARE</span>
      </div>
    </div>
  </section>

  <section class="card card-back" aria-label="Card back">
    <div class="back-mark">
      <span class="back-mark-dot" aria-hidden="true"></span>
      <span>Ridgeline Pet Vision Care</span>
    </div>
    <div class="contact">
      <p class="name">Delia Vossman, <span class="creds">BSc, DVM, MSc, DipACVO</span></p>
      <p class="role">Veterinary Ophthalmologist</p>
      <p>1874 Thornbury Rd</p>
      <p class="address">Kelowna, BC, V1X 4M9</p>
      <p>250.418.3927</p>
      <p>ridgelinepetvisioncare@mailbox-example.net</p>
      <p>www.ridgelinepetvisioncare-example.net</p>
    </div>
  </section>
</main>
</body>
</html>
```